Business Card Design - Photographer

I am a landscape photographer and I require a business card design. 

I require two designs:
1)  a double sided business card
 and
b)  a single sided business card 

The single sided design can either be the same as the double sided (with just one side having all the information)....or it can be an entire new design. Its up to you.

My corporate colours are (CMYK):

Blue   69, 32, 0, 0
Grey  72,  64,  47,  31
Green  32,  2,  91,  0
Yellow   0, 19, 92, 0
Orange  0, 39, 75, 0

Colour space in final file should be in CMYK.

The details that need to be included on the card:

- Use the provided Logo
- Name: Wiktor Baranowski
- Email:   sales@vistalumeworks.com.au
- Website:    vistalumeworks.com.au
- Twitter:    twitter.com/vistalumeworks
- Facebook:   facebook.com/vistalumeworks
- Mobile  0417 539 662

Please use the attached template to design the logo to the specified size, including the marked bleed lines. I have also attached my logo in PNG (transparent background) and ai format for you to use.

The final file should be:
- Photoshop version with layers so I can edit the name/text etc. All non vector files should be high resolution at 1039 x 697 pixels at 300 dpi.

I also require a file as:
- Vector based PDF

Anyway questions please contact me.

Thank you

Industry/Entity Type

Landscape

Logo styles of interest
Pictorial/Combination Logo
Abstract Logo
Wordmark Logo
Lettermark Logo
Requirements
Must have
• The details that need to be included on the card:

- Use the provided Logo
- Name: Wiktor Baranowski
- Email: sales@vistalumeworks.com.au
- Website: vistalumeworks.com.au
- Twitter: twitter.com/vistalumeworks
- Facebook: facebook.com/vistalumeworks
- Mobile 0417 539 662

```html
<!DOCTYPE html>
<html lang="en">
<head>
<meta charset="utf-8">
<title>Vistalume Works – Business Card</title>
<link rel="stylesheet" href="https://fonts.googleapis.com/css2?family=Open+Sans:wght@400;600;700&display=swap">
<style>
  :root {
    --stage: #2d3335;
    --card: #ffffff;
    --brand-blue: #3d8fcf;
    --brand-grey: #3c4050;
    --brand-green: #b5cf3a;
    --brand-orange: #f6a54b;
    --text-dark: #3a3a3a;
    --text-light: #ffffff;
  }
  * { box-sizing: border-box; margin: 0; padding: 0; }
  html, body {
    width: 987px; height: 1200px; overflow: hidden;
    background: var(--stage);
    font-family: "Open Sans", Arial, sans-serif;
  }
  .canvas { position: relative; width: 987px; height: 1200px; }
  .card {
    position: absolute; left: 98px; width: 789px; height: 452px;
    background: var(--card); border-radius: 32px; overflow: hidden;
  }
  .card--front { top: 118px; }
  .card--back { top: 630px; }

  .holder {
    position: absolute; top: 14px; left: 0; width: 100%;
    text-align: center; color: var(--text-dark);
  }
  .holder__name { font-size: 29px; font-weight: 700; }
  .holder__role { font-size: 18px; font-weight: 400; }

  .brand-mark {
    position: absolute; border-radius: 50%; background: var(--brand-grey);
  }
  .card--front .brand-mark { left: 330px; top: 67px; width: 134px; height: 134px; }
  .brand-name {
    position: absolute; color: var(--brand-grey);
    font-weight: 600; letter-spacing: 2px; white-space: nowrap;
  }
  .card--front .brand-name {
    top: 212px; left: 0; width: 100%; text-align: center; font-size: 32px;
  }

  .swoosh-band {
    position: absolute; left: 0; right: 0; top: 300px; bottom: 0;
    background: linear-gradient(180deg, var(--brand-grey) 0%, var(--brand-blue) 20%, var(--brand-blue) 100%);
  }

  .contact {
    position: absolute; color: var(--text-light);
    font-size: 17px; line-height: 25px;
  }
  .contact b { font-weight: 700; }
  .contact--social { left: 42px; bottom: 20px; }
  .contact--direct { right: 34px; bottom: 20px; text-align: right; }

  .card--back .brand-mark { left: 18px; top: 45px; width: 345px; height: 345px; }
  .card--back .brand-name { left: 392px; top: 196px; font-size: 34px; }
  .back-url {
    position: absolute; right: 38px; bottom: 30px;
    font-size: 33px; color: var(--text-dark);
  }
</style>
</head>
<body>
<main class="canvas">
  <section class="card card--front">
    <div class="swoosh-band" role="img" aria-label="Decorative swoosh band in grey, green, orange and blue"></div>
    <div class="holder">
      <span class="holder__name">Your Name -</span>
      <span class="holder__role">Adminsitrator</span>
    </div>
    <div class="brand-mark"></div>
    <div class="brand-name">VISTALUME WORKS</div>
    <div class="contact contact--social">
      <div><b>t</b> : twitter.com/vistalumeworks</div>
      <div><b>f</b> : facebook.com/vistalumeworks</div>
    </div>
    <div class="contact contact--direct">
      <div><b>m</b> : 0417 539 662</div>
      <div><b>e</b> : sales@vistalumeworks.com.au</div>
      <div><b>w</b> : vistalumeworks.com.au</div>
    </div>
  </section>

  <section class="card card--back">
    <div class="brand-mark"></div>
    <div class="brand-name">VISTALUME WORKS</div>
    <div class="back-url">www.vistalumeworks.com.au</div>
  </section>
</main>
</body>
</html>
```